Marlow Estate Fixers (Handyman / Home Improvement Company)

Looking for a double sided professional looking business card with Logo attached to be highlighted on one side and throwing in an image of a handyman as an option would be nice to see as well. We are a company focused on providing quality Handyman and Home improvement services in a timely manner that is done right the first time with integrity

Industry/Entity Type

Handyman / Home Improvement

Contact Information for Business Card

(LOGO, Name, Mobile and office phone numbers, email) on front side of card, (the words "The SOLUTION to all of your Handyman and Home Improvement needs" followed by "Family Owned and Operated" at the very bottom) on the back.

Colors
EB3D1F
EC4F4E
F09395
F8D3D4
FCEDEE

Requirements
Must have
• Red, Gray, Black Color scheme
Should not have
• No Yellow or Blue colors

```html
<!DOCTYPE html>
<html lang="en">
<head>
<meta charset="utf-8">
<title>Marlow Estate Fixers – Business Card</title>
<link href="https://fonts.googleapis.com/css2?family=Michroma&family=Poppins:wght@400;500;600&display=swap" rel="stylesheet">
<style>
  :root {
    --page: #e7e8ea;
    --card: #030405;
    --red: #eb2a2e;
    --red-soft: #f09395;
    --blush: #fcedee;
    --grey: #a7a9ac;
    --white: #ffffff;
    --figure-a: #3a2a28;
    --figure-b: #7a2a24;
  }
  * { margin: 0; padding: 0; box-sizing: border-box; }
  html, body { width: 1194px; height: 1200px; overflow: hidden; }
  body { background: var(--page); position: relative; font-family: "Poppins", sans-serif; }

  .card {
    position: absolute; left: 308px; width: 580px; height: 331px;
    background: var(--card); overflow: hidden;
  }
  .card--front { top: 166px; }
  .card--back { top: 639px; }

  .handyman-art {
    position: absolute; left: 22px; top: 11px; width: 182px; height: 301px;
    border-radius: 60px 60px 0 0;
    background: linear-gradient(180deg, #c8322c 0%, #2a2a2a 35%, #222 70%, #2f5a99 100%);
  }
  .card--back .handyman-art {
    background: linear-gradient(180deg, var(--figure-b) 0%, var(--figure-a) 40%, #1d1d1f 70%, #1f2738 100%);
    opacity: .9;
  }

  .brand-name {
    position: absolute; font-family: "Michroma", sans-serif; color: var(--red);
    letter-spacing: 1px; line-height: 1.25;
  }
  .card--front .brand-name { right: 39px; top: 48px; font-size: 17px; text-align: right; }
  .card--back .brand-name { left: 0; right: 0; top: 100px; font-size: 24px; text-align: center; }

  .person-name {
    position: absolute; right: 31px; top: 163px; font-family: "Michroma", sans-serif;
    font-size: 18px; color: var(--red); letter-spacing: 2px; font-weight: 400;
  }
  .person-role {
    position: absolute; right: 31px; top: 191px; font-size: 13px; color: var(--white);
    letter-spacing: 2px; font-weight: 500;
  }
  .title-rule {
    position: absolute; left: 202px; width: 278px; top: 203px; height: 1px; background: #cfd0d2;
  }
  .contact-list { position: absolute; right: 33px; top: 222px; list-style: none; }
  .contact-item {
    display: flex; align-items: center; justify-content: flex-end; gap: 12px;
    height: 29.5px; font-size: 12.5px; color: var(--white); letter-spacing: .8px;
  }
  .contact-item svg { width: 17px; height: 17px; }

  .tagline {
    position: absolute; left: 0; right: 0; top: 219px; text-align: center;
    font-family: "Michroma", sans-serif; font-size: 13px; line-height: 26px;
    color: var(--grey); letter-spacing: 3.4px;
  }
  .family-note {
    position: absolute; left: 0; right: 0; top: 282px; text-align: center;
    font-size: 12.5px; font-weight: 600; color: var(--red); letter-spacing: 2.6px;
  }

  .base-band { position: absolute; left: 0; bottom: 0; width: 580px; height: 19px; }
</style>
</head>
<body>

<svg width="0" height="0" style="position:absolute">
  <defs>
    <linearGradient id="bandGradient" x1="0" x2="1" y1="0" y2="0">
      <stop offset="0" stop-color="#fcedee"/>
      <stop offset=".35" stop-color="#f8d3d4"/>
      <stop offset=".6" stop-color="#f09395"/>
      <stop offset=".8" stop-color="#ec4f4e"/>
      <stop offset="1" stop-color="#eb2a2e"/>
    </linearGradient>
  </defs>
</svg>

<section class="card card--front">
  <div class="handyman-art" role="img" aria-label="Illustration of a smiling handyman in cap and polo with arms crossed holding a hammer"></div>

  <div class="brand-name">MARLOW ESTATE<br>FIXERS</div>

  <h1 class="person-name">DANA WHITCOMBE</h1>
  <div class="person-role">OWNER</div>
  <div class="title-rule"></div>

  <ul class="contact-list">
    <li class="contact-item">(555) 014-2386
      <svg viewBox="0 0 20 20" aria-hidden="true"><circle cx="10" cy="10" r="8.5" fill="none" stroke="#eb2a2e" stroke-width="1.2"/><path d="M7 6.2l1.4-.4 1 2.2-.9.8a5 5 0 0 0 2.6 2.6l.8-.9 2.2 1-.4 1.4c-3.4.2-6.9-3.3-6.7-6.7z" fill="none" stroke="#eb2a2e" stroke-width="1"/></svg>
    </li>
    <li class="contact-item">(555) 014-2386
      <svg viewBox="0 0 20 20" aria-hidden="true"><circle cx="10" cy="10" r="8.5" fill="none" stroke="#eb2a2e" stroke-width="1.2"/><rect x="7.3" y="5.3" width="5.4" height="9.4" rx="1" fill="none" stroke="#eb2a2e" stroke-width="1"/></svg>
    </li>
    <li class="contact-item">danawhitcombe@example.com
      <svg viewBox="0 0 20 20" aria-hidden="true"><circle cx="10" cy="10" r="8.5" fill="none" stroke="#eb2a2e" stroke-width="1.2"/><rect x="5.8" y="7" width="8.4" height="6" fill="none" stroke="#eb2a2e" stroke-width="1"/><path d="M5.8 7l4.2 3.3L14.2 7" fill="none" stroke="#eb2a2e" stroke-width="1"/></svg>
    </li>
  </ul>

  <svg class="base-band" viewBox="0 0 580 19" aria-hidden="true">
    <rect x="0" y="0" width="580" height="19" fill="url(#bandGradient)"/>
    <polygon points="0,5 323,5 313,15 0,15" fill="#030405"/>
    <rect x="0" y="8.5" width="313" height="3" fill="#fcedee"/>
  </svg>
</section>

<section class="card card--back">
  <div class="handyman-art" role="img" aria-label="Faded illustration of the handyman mascot in the background"></div>

  <div class="brand-name">MARLOW ESTATE FIXERS</div>

  <p class="tagline">YOUR SOLUTION TO ALL OF YOUR HANDYMAN<br>AND HOME IMPROVEMENT NEEDS</p>
  <p class="family-note">Family Owned and Operated</p>

  <svg class="base-band" viewBox="0 0 580 19" aria-hidden="true">
    <rect x="0" y="0" width="580" height="19" fill="url(#bandGradient)"/>
    <polygon points="0,5 323,5 313,15 0,15" fill="#030405"/>
    <rect x="0" y="8.5" width="313" height="3" fill="#fcedee"/>
  </svg>
</section>

</body>
</html>
```